Talon Microsystems PowerPoint Master Slide Deck Design

This is a 2-phase project to design a slide deck for a semiconductor company in the Silicon Valley. The design budget will be increased with each phase.
The slide deck will need to have one version with a dark background for presentations and a second version with a white background. Otherwise, the slides will be the same. I anticipate we will need a total of 10 slides, but that number may change.
The first phase will be to design a Title and a Title and Content slide.
- The Title Slide is the first slide of the deck. It should include the presentation title, the presenter's name and date of presentation
- The Title and Content slide should include a title and content with bullet points and up to 2 additional sub-bullets
- The Title and Content slide should have a footer that includes the slide #, Talon Microsystems Confidential, and the logo. This footer will be on every slide except the Title Slide
The first two slides will serve as the format for the remaining ~8 slides:
-Header and Content Text (1, 2, 4 column)
-Header and Content Image (bar chart, pie chart, tables)
-Break
-Title only
-Closing (Talon logo only)
Our slides contain a lot of content so a clean and simple design is best.
Both phases will need to include pre-set color options for
-Text and Lines
-Shadows
-Bullets and sub-bullets (including shapes, ex. circle, slash, square, etc.)
-Bar charts, pie charts, tables
Samples of our collateral are attached. Logo files are also attached
Look and feel
Each slider illustrates characteristics of the customer's brand and the style your logo design should communicate.

```html
<!DOCTYPE html>
<html lang="en">
<head>
<meta charset="utf-8">
<title>Talon Microsystems Slide Master</title>
<link href="https://fonts.googleapis.com/css2?family=Red+Hat+Display:wght@400;500;700&family=Open+Sans:wght@400;600&display=swap" rel="stylesheet">
<style>
:root{
  --ink:#1f1f24;
  --muted:#5a5d66;
  --blue:#0a4fe0;
  --blue-mid:#1377ea;
  --cyan:#12aef2;
  --paper:#ffffff;
  --mist:#eef3f8;
  --deep:#0c2a5c;
  --navy:#07153a;
  --teal:#1e6f86;
}
*{margin:0;padding:0;box-sizing:border-box}
html,body{width:1200px;height:4155px;overflow:hidden;background:var(--paper)}
body{position:relative;font-family:"Open Sans",sans-serif;color:var(--ink)}
.slide{position:absolute;left:53px;width:1088px;height:611px;background:var(--paper);box-shadow:0 2px 8px rgba(0,0,0,.18);overflow:hidden}
.brand{position:absolute;display:flex;align-items:center;gap:10px;font-family:"Red Hat Display",sans-serif;font-weight:700;color:var(--blue);white-space:nowrap}
.brand-dot{border-radius:50%;border:3px solid var(--blue);flex:none}
.heading{font-family:"Red Hat Display",sans-serif;font-weight:700;color:var(--ink)}
.underlined{border-bottom:2px solid var(--blue-mid);padding-bottom:6px}
.footer-note{position:absolute;font-size:11px;line-height:14px;color:var(--ink);white-space:nowrap;z-index:2}
.slide .brand.footer-brand{left:auto;right:12px;transform:none;font-size:15px;gap:6px;z-index:2}
.slide .brand.footer-brand .brand-dot{width:12px;height:12px;border-width:2px}
/* slide 1 */
.s-title{top:59px}
.s-title .brand{left:11px;top:245px;font-size:34px}
.s-title .brand-dot{width:28px;height:28px}
.s-title .deco{position:absolute;left:500px;top:30px;width:560px;height:560px;border-radius:50%;background:radial-gradient(circle at 60% 35%,#e7f4ff,#f4f8ff 70%)}
.s-title h1{position:absolute;left:11px;top:305px;font-size:38px}
.s-title .presenter{position:absolute;left:11px;top:352px;font-family:"Red Hat Display",sans-serif;font-size:22px;color:var(--ink)}
.s-title .presenter span{color:var(--blue-mid)}
.s-title .date{position:absolute;left:11px;top:382px;font-family:"Red Hat Display",sans-serif;font-size:21px}
/* slide 2 */
.s-columns{top:733px}
.s-columns .bg{position:absolute;inset:0;background:linear-gradient(180deg,#f3f6fa 0%,#e3ebf3 55%,#cfdbe6 100%)}
.s-columns .brand.header-brand{left:50%;transform:translateX(-50%);top:34px;font-size:24px}
.s-columns .header-brand .brand-dot{width:20px;height:20px}
.s-columns h2{position:absolute;left:50%;transform:translateX(-50%);top:108px;font-size:22px;white-space:nowrap}
.col{position:absolute;top:216px;width:272px}
.col.card{background:var(--paper);box-shadow:0 0 6px rgba(0,0,0,.15);border-bottom:3px solid var(--blue-mid);top:195px;left:382px;width:317px;height:336px;padding:21px 19px}
.col h3{font-family:"Red Hat Display",sans-serif;font-size:13px;font-weight:700;margin-bottom:4px}
.col .lead{font-size:13px;line-height:20px;margin-bottom:14px}
.col ul{list-style:none}
.col li{position:relative;padding-left:8px;font-size:9.5px;line-height:15.5px;color:var(--muted);margin-bottom:16px}
.col li::before{content:"";position:absolute;left:0;top:6px;width:4px;height:4px;border-radius:50%;background:var(--blue)}
/* slide 3 */
.s-image-text{top:1411px;left:48px;width:1093px}
.s-image-text .photo{position:absolute;left:0;top:0;width:512px;height:611px;background:radial-gradient(circle at 62% 62%,#d8c59a 0,#4fa3b5 12%,#1e6f86 35%,#0b2e3e 75%);clip-path:ellipse(511px 400px at 0 50%)}
.s-image-text .brand.header-brand{left:551px;top:24px;font-size:26px}
.s-image-text .header-brand .brand-dot{width:20px;height:20px}
.s-image-text h2{position:absolute;left:549px;top:110px;font-size:22px}
.s-image-text .copy{position:absolute;left:549px;top:163px;width:505px}
.s-image-text p{font-size:10.3px;line-height:18px;color:var(--muted);margin-bottom:18px}
/* slide 4 */
.s-text{top:2090px}
.s-text .brand.header-brand{left:14px;top:24px;font-size:26px}
.s-text .header-brand .brand-dot{width:20px;height:20px}
.s-text h2{position:absolute;right:12px;top:18px;font-size:22px}
.s-text .copy{position:absolute;left:14px;top:90px;width:1062px}
.s-text p{font-size:9.6px;line-height:20.3px;color:var(--muted);margin-bottom:40px;text-align:justify}
/* slide 5 */
.s-break{top:2770px}
.s-break .brand.top{left:11px;top:28px;font-size:26px}
.s-break .brand-dot{width:20px;height:20px}
.s-break h2{position:absolute;left:64px;top:286px;font-size:32px;padding-bottom:10px;border-bottom:2px solid var(--blue-mid)}
.s-break .brand.bottom{left:494px;top:536px;font-size:26px}
.s-break .chip{position:absolute;left:584px;top:0;width:504px;height:611px;background:radial-gradient(circle at 52% 50%,#bfe8ff 0,#2c86e8 14%,#0d3f9e 42%,var(--navy) 85%);clip-path:ellipse(560px 470px at 100% 50%)}
/* slide 6 */
.s-closing{top:3450px}
.s-closing .deco{position:absolute;left:310px;top:-10px;width:480px;height:480px;border-radius:50%;background:#f3f7fd}
.s-closing .brand{left:50%;transform:translateX(-50%);top:232px;font-size:40px}
.s-closing .brand-dot{width:30px;height:30px}
.s-closing h2{position:absolute;left:0;right:0;top:338px;text-align:center;font-size:32px}
</style>
</head>
<body>

<section class="slide s-title">
  <div class="deco"></div>
  <div class="brand"><span class="brand-dot"></span>Talon Microsystems</div>
  <h1 class="heading">Lorem ipsum dolor sit</h1>
  <p class="presenter">Marcus <span>Ellery</span></p>
  <p class="date">13.12.2023</p>
</section>

<section class="slide s-columns">
  <div class="bg" role="img" aria-label="Soft circuit board background"></div>
  <div class="brand header-brand"><span class="brand-dot"></span>Talon Microsystems</div>
  <h2 class="heading underlined">Lorem ipsum dolor sit amet</h2>

  <div class="col" style="left:75px">
    <h3>Lorem ipsum</h3>
    <p class="lead">Lorem ipsum dolor sit met, consectetur adipscing elit, lacus vel facilisis.</p>
    <ul>
      <li>Lorem ipsum dolor sit met, consectetur adipscing elit, lacus vel facilisis. Lorem ipsum dolor sit met, consectetur adipscing elit, lacus vel facilisis. Lorem ipsum dolor sit met, consectetur adipscing.</li>
      <li>Lorem ipsum dolor sit met, consectetur adipscing elit, lacus vel facilisis. Lorem ipsum dolor sit met, consectetur adipscing elit, lacus vel facilisis. Lorem ipsum dolor sit met, consectetur adipscing.</li>
      <li>Lorem ipsum dolor sit met, consectetur adipscing elit, lacus vel facilisis. Lorem ipsum dolor sit met, consectetur adipscing elit, lacus vel facilisis. Lorem ipsum dolor sit met, consectetur adipscing.</li>
    </ul>
  </div>
  <div class="col card">
    <h3>Lorem ipsum</h3>
    <p class="lead">Lorem ipsum dolor sit met, consectetur adipscing elit, lacus vel facilisis.</p>
    <ul>
      <li>Lorem ipsum dolor sit met, consectetur adipscing elit, lacus vel facilisis. Lorem ipsum dolor sit met, consectetur adipscing elit, lacus vel facilisis. Lorem ipsum dolor sit met, consectetur adipscing.</li>
      <li>Lorem ipsum dolor sit met, consectetur adipscing elit, lacus vel facilisis. Lorem ipsum dolor sit met, consectetur adipscing elit, lacus vel facilisis. Lorem ipsum dolor sit met, consectetur adipscing.</li>
      <li>Lorem ipsum dolor sit met, consectetur adipscing elit, lacus vel facilisis. Lorem ipsum dolor sit met, consectetur adipscing elit, lacus vel facilisis. Lorem ipsum dolor sit met, consectetur adipscing.</li>
    </ul>
  </div>
  <div class="col" style="left:752px">
    <h3>Lorem ipsum</h3>
    <p class="lead">Lorem ipsum dolor sit met, consectetur adipscing elit, lacus vel facilisis.</p>
    <ul>
      <li>Lorem ipsum dolor sit met, consectetur adipscing elit, lacus vel facilisis. Lorem ipsum dolor sit met, consectetur adipscing elit, lacus vel facilisis. Lorem ipsum dolor sit met, consectetur adipscing.</li>
      <li>Lorem ipsum dolor sit met, consectetur adipscing elit, lacus vel facilisis. Lorem ipsum dolor sit met, consectetur adipscing elit, lacus vel facilisis. Lorem ipsum dolor sit met, consectetur adipscing.</li>
      <li>Lorem ipsum dolor sit met, consectetur adipscing elit, lacus vel facilisis. Lorem ipsum dolor sit met, consectetur adipscing elit, lacus vel facilisis. Lorem ipsum dolor sit met, consectetur adipscing.</li>
    </ul>
  </div>

  <p class="footer-note" style="left:13px;top:573px">Talon Microsystems Confidential</p>
  <div class="brand footer-brand" style="top:569px"><span class="brand-dot"></span>Talon</div>
</section>

<section class="slide s-image-text">
  <div class="photo" role="img" aria-label="Engineer inspecting a circuit board in a cleanroom"></div>
  <div class="brand header-brand"><span class="brand-dot"></span>Talon Microsystems</div>
  <h2 class="heading underlined">Lorem ipsum dolor sit amet</h2>
  <div class="copy">
    <p>Lorem ipsum dolor sit amet, consectetur adipiscing elit, sed do eiusmod tempor incididunt ut labore et dolore magna aliqua. Quis ipsum suspendisse ultrices gravida. Risus commodo viverra umsan lacus vel facilisis. Lorem ipsum dolor sit amet, consectetur adipiscing elit, sed do eiusmod tempor incididunt ut labore et dolore magna aliqua. Quis ipsum suspendisse ultrices gravida. Risus commodo viverra umsan lacus vel facilisis.</p>
    <p>Lorem ipsum dolor sit amet, consectetur adipiscing elit, sed do eiusmod tempor incididunt ut labore et dolore magna aliqua. Quis ipsum suspendisse ultrices gravida. Risus commodo viverra umsan lacus vel facilisis. Lorem ipsum dolor sit amet, consectetur adipiscing elit, sed do eiusmod tempor incididunt ut labore et dolore magna aliqua. Quis ipsum suspendisse ultrices gravida. Risus commodo viverra umsan lacus vel facilisis.</p>
    <p>Lorem ipsum dolor sit amet, consectetur adipiscing elit, sed do eiusmod tempor incididunt ut labore et dolore magna aliqua. Quis ipsum suspendisse ultrices gravida. Risus commodo viverra umsan lacus vel facilisis. Lorem ipsum dolor sit amet, consectetur adipiscing elit, sed do eiusmod tempor incididunt ut labore et dolore magna aliqua. Quis ipsum suspendisse ultrices gravida. Risus commodo viverra umsan lacus vel facilisis.</p>
    <p>Lorem ipsum dolor sit amet, consectetur adipiscing elit, sed do eiusmod tempor incididunt ut labore et dolore magna aliqua. Quis ipsum suspendisse ultrices gravida. Risus commodo viverra umsan lacus vel facilisis. Lorem ipsum dolor sit amet, consectetur adipiscing elit, sed do eiusmod tempor incididunt ut labore et dolore magna aliqua. Quis ipsum suspendisse ultrices gravida.</p>
  </div>
  <p class="footer-note" style="left:382px;top:578px">Talon Microsystems Confidential</p>
  <div class="brand footer-brand" style="top:574px"><span class="brand-dot"></span>Talon</div>
</section>

<section class="slide s-text">
  <div class="brand header-brand"><span class="brand-dot"></span>Talon Microsystems</div>
  <h2 class="heading underlined">Lorem ipsum dolor sit amet</h2>
  <div class="copy">
    <p>Lorem ipsum dolor sit amet, consectetur adipiscing elit, sed do eiusmod tempor incididunt ut labore et dolore magna aliqua. Quis ipsum suspendisse ultrices gravida. Risus commodo viverra umsan lacus vel facilisis rem ipsum dolor sit amet, consectetur adipiscing elit, sed do eiusmod tempor incididunt ut labore et dolore magna aliqua. Quis ipsum suspendisse ultrices gravida. Risus commodo viverra umsan lacus vel facilisis. Lorem ipsum dolor sit amet, consectetur adipiscing elit, sed do eiusmod tempor incididunt ut labore et dolore magna aliqua. Quis ipsum suspendisse ultrices gravida. Risus commodo viverra umsan lacus vel facilisis. Lorem ipsum dolor sit amet, consectetur adipiscing elit, sed do eiusmod tempor incididunt ut labore et dolore magna aliqua. Quis ipsum suspendisse ultrices gravida. Risus commodo viverra umsan lacus vel facilisis. Lorem ipsum dolor sit amet, consectetur adipiscing elit, sed do eiusmod tempor incididunt ut labore et dolore magna aliqua. Quis ipsum suspendisse ultrices gravida. Risus commodo viverra umsan lacus vel facilisis. Lorem ipsum dolor sit amet, etur adipiscing elit, sed do eiusmod tempor incididunt ut labore et dolore magna aliqua. Quis ipsum suspendisse ultrices gravida. Risus commodo viverra umsan lacus vel facilisis.</p>
    <p>Lorem ipsum dolor sit amet, consectetur adipiscing elit, sed do eiusmod tempor incididunt ut labore et dolore magna aliqua. Quis ipsum suspendisse ultrices gravida. Risus commodo viverra umsan lacus vel facilisis rem ipsum dolor sit amet, consectetur adipiscing elit, sed do eiusmod tempor incididunt ut labore et dolore magna aliqua. Quis ipsum suspendisse ultrices gravida. Risus commodo viverra umsan lacus vel facilisis. Lorem ipsum dolor sit amet, consectetur adipiscing elit, sed do eiusmod tempor incididunt ut labore et dolore magna aliqua. Quis ipsum suspendisse ultrices gravida. Risus commodo viverra umsan lacus vel facilisis. Lorem ipsum dolor sit amet, consectetur adipiscing elit, sed do eiusmod tempor incididunt ut labore et dolore magna aliqua. Quis ipsum suspendisse ultrices gravida. Risus commodo viverra umsan lacus vel facilisis. Lorem ipsum dolor sit amet, consectetur adipiscing elit, sed do eiusmod tempor incididunt ut labore et dolore magna aliqua. Quis ipsum suspendisse ultrices gravida. Risus commodo viverra umsan lacus vel facilisis. Lorem ipsum dolor sit amet, etur adipiscing elit, sed do eiusmod tempor incididunt ut labore et dolore magna aliqua. Quis ipsum suspendisse ultrices gravida. Risus commodo viverra umsan lacus vel facilisis.</p>
    <p>Lorem ipsum dolor sit amet, consectetur adipiscing elit, sed do eiusmod tempor incididunt ut labore et dolore magna aliqua. Quis ipsum suspendisse ultrices gravida. Risus commodo viverra umsan lacus vel facilisis rem ipsum dolor sit amet, consectetur adipiscing elit, sed do eiusmod tempor incididunt ut labore et dolore magna aliqua. Quis ipsum suspendisse ultrices gravida. Risus commodo viverra umsan lacus vel facilisis. Lorem ipsum dolor sit amet, consectetur adipiscing elit, sed do eiusmod tempor incididunt ut labore et dolore magna aliqua. Quis ipsum suspendisse ultrices gravida. Risus commodo viverra umsan lacus vel facilisis. Lorem ipsum dolor sit amet, consectetur adipiscing elit, sed do eiusmod tempor incididunt ut labore et dolore magna aliqua. Quis ipsum suspendisse ultrices gravida. Risus commodo viverra umsan lacus vel facilisis. Lorem ipsum dolor sit amet, consectetur adipiscing elit, sed do eiusmod tempor incididunt ut labore et dolore magna aliqua. Quis ipsum suspendisse ultrices gravida. Risus commodo viverra umsan lacus vel facilisis. Lorem ipsum dolor sit amet, etur adipiscing elit, sed do eiusmod tempor incididunt ut labore et dolore magna aliqua. Quis ipsum suspendisse ultrices gravida. Risus commodo viverra umsan lacus vel facilisis.</p>
  </div>
  <p class="footer-note" style="left:16px;top:570px">Talon Microsystems Confidential</p>
  <div class="brand footer-brand" style="top:566px"><span class="brand-dot"></span>Talon</div>
</section>

<section class="slide s-break">
  <div class="chip" role="img" aria-label="Glowing microchip on a blue circuit board"></div>
  <div class="brand top"><span class="brand-dot"></span>Talon Microsystems</div>
  <h2 class="heading">Lorem ipsum dolor sit amet</h2>
  <p class="footer-note" style="left:11px;top:565px">Talon Microsystems Confidential</p>
  <div class="brand bottom"><span class="brand-dot"></span>Talon</div>
</section>

<section class="slide s-closing">
  <div class="deco"></div>
  <div class="brand"><span class="brand-dot"></span>Talon Microsystems</div>
  <h2 class="heading">Thank You Talon Microsystems</h2>
</section>

</body>
</html>
```